Thornvale Group needs a business card design

We need a new business card design using the logo recently selected in a logo competition on Pixel Bazaar. Our business is a consultancy specializing in aviation and energy and the winning business card design will promote an image of precision and professionalism with creativity.

Please use the logo with the name on the front of the card and use a complementary font. Make the back white with either the light grey or dark grey logo.

Target Market(s)

Senior finance and legal leaders at aviation and energy companies

Industry/Entity Type

Management Consulting

Contact Information for Business Card

Peter Castrell
President
Thornvale Group

www.thornvalegroup.example

(555) 204-6391
pc@thornvalegroup.example

Requirements
Must have
• Professional font that goes well with the logo font

```html
<!DOCTYPE html>
<html lang="en">
<head>
<meta charset="utf-8">
<title>Thornvale Group — Business Card</title>
<link rel="stylesheet" href="https://fonts.googleapis.com/css2?family=Open+Sans:wght@400;600&display=swap">
<style>
  :root {
    --stage: #000000;
    --card: #ffffff;
    --navy: #1b3a6b;
    --ink: #1a1a1a;
    --grey: #555555;
  }
  * { margin: 0; padding: 0; box-sizing: border-box; }
  html, body {
    width: 1200px; height: 900px; overflow: hidden;
    background: var(--stage);
    font-family: "Open Sans", Arial, sans-serif;
  }
  .stage { position: relative; width: 1200px; height: 900px; }

  .card {
    position: absolute;
    background: var(--card);
    width: 477px; height: 293px;
  }
  .card--front { left: 116px; top: 275px; border-radius: 0 62px 0 62px; }
  .card--back  { left: 622px; top: 276px; height: 292px; border-radius: 62px 0 62px 0; }

  /* Front */
  .brand-mark {
    position: absolute; left: 50%; top: 36px;
    width: 46px; height: 46px; margin-left: -23px;
    background: var(--navy);
  }
  .brand-name {
    position: absolute; left: 0; right: 0;
    text-align: center; color: var(--navy);
    font-weight: 400; letter-spacing: 1px;
  }
  .card--front .brand-name { top: 132px; font-size: 32px; }

  .holder {
    position: absolute; right: 263px; top: 224px; text-align: right;
  }
  .holder__name { font-size: 17px; font-weight: 600; color: var(--navy); line-height: 22px; }
  .holder__title { font-size: 13px; color: var(--ink); line-height: 22px; }

  .contact { position: absolute; left: 245px; top: 226px; list-style: none; }
  .contact li {
    display: flex; align-items: center; gap: 9px;
    font-size: 13px; color: var(--ink); height: 21px;
  }
  .contact svg { width: 10px; height: 10px; fill: var(--navy); }

  /* Back */
  .card--back .brand-name { top: 78px; font-size: 36px; }

  .services-title {
    position: absolute; right: 259px; top: 197px;
    text-align: right; color: var(--navy);
    font-size: 15px; font-weight: 600; line-height: 21.5px;
  }
  .services-title span { display: block; text-decoration: underline; text-underline-offset: 3px; }

  .sectors { position: absolute; left: 250px; top: 197px; list-style: none; }
  .sectors li {
    display: flex; align-items: center; gap: 9px;
    font-size: 14px; font-weight: 600; color: var(--ink); line-height: 23px;
  }
  .sectors li::before {
    content: ""; width: 6px; height: 6px; background: var(--navy);
  }
</style>
</head>
<body>
<main class="stage">
  <section class="card card--front" aria-label="Card front">
    <div class="brand-mark" aria-hidden="true"></div>
    <p class="brand-name">Thornvale Group</p>

    <div class="holder">
      <p class="holder__name">Peter J. Castrell</p>
      <p class="holder__title">President</p>
    </div>

    <ul class="contact">
      <li>
        <svg viewBox="0 0 10 10" aria-hidden="true"><path d="M2 0.5 L3.6 0.5 L4.3 2.8 L3.2 3.8 Q4.3 6 6.2 6.8 L7.2 5.7 L9.5 6.4 L9.5 8 Q9 9.5 7.5 9.5 Q1 8.5 0.5 2 Q0.5 0.8 2 0.5 Z"/></svg>
        (555) 204-6391
      </li>
      <li>
        <svg viewBox="0 0 10 10" aria-hidden="true"><path d="M0.5 2 L9.5 2 L9.5 8.5 L0.5 8.5 Z M1.2 2.6 L5 5.6 L8.8 2.6" stroke="#fff" stroke-width="0.8"/></svg>
        pc@thornvalegroup.example
      </li>
    </ul>
  </section>

  <section class="card card--back" aria-label="Card back">
    <p class="brand-name">Thornvale Group</p>

    <h2 class="services-title">
      <span>FINANCE AND</span>
      <span>STRATEGY</span>
      <span>CONSULTING</span>
    </h2>

    <ul class="sectors">
      <li>Aviation</li>
      <li>Manufacturing</li>
      <li>Energy</li>
    </ul>
  </section>
</main>
</body>
</html>
```